Business Card Design for Marketing Firm

Looking for business card design for higher end marketing firm. Clean but impressionable/trendy. We are a marketing firm that represents manufacturers in the foodservice equipment and supply industry. Our customers are end users such has hotels, restaurants, country clubs, convention centers and casinos as well as distributors of restaurants supplies and equipment, and manufacturers of foodservice equipment and supplies.
Target Market(s)
Hotels, Restaurants, Supply & Equipment Distributors, Foodservice Manufacturers
Industry/Entity Type
Foodservice/Hospitality
Contact Information for Business Card
Name, Title, Contact Number, Email, Website, Social Media, Address
Requirements
Must have
- Clean & Simple but Serious and Impressionable

```html
<!DOCTYPE html>
<html lang="en">
<head>
<meta charset="utf-8">
<title>Beacon Hospitality Reps — Business Card</title>
<link href="https://fonts.googleapis.com/css2?family=Cinzel:wght@600&family=Montserrat:wght@400;700&display=swap" rel="stylesheet">
<style>
  :root {
    --backdrop: #e6e6e6;
    --navy-deep: #27256a;
    --navy-soft: #3d3e86;
    --navy-ink: #25246c;
    --paper: #f6f6f7;
    --paper-shade: #ececee;
    --grey-text: #7a7a80;
    --white: #ffffff;
  }
  * { margin: 0; padding: 0; box-sizing: border-box; }
  html, body { width: 1200px; height: 1200px; overflow: hidden; }
  body {
    background: var(--backdrop);
    font-family: "Montserrat", Arial, sans-serif;
    position: relative;
  }
  .card {
    position: absolute;
    left: 234px;
    width: 730px;
    height: 417px;
  }
  .card-front {
    top: 160px;
    background: linear-gradient(100deg, var(--navy-deep) 0%, var(--navy-soft) 100%);
    display: flex;
    align-items: center;
    justify-content: center;
  }
  .front-wordmark {
    font-family: "Cinzel", Georgia, serif;
    font-weight: 600;
    color: var(--white);
    text-align: right;
    line-height: 1.1;
  }
  .front-wordmark .name-main { display: block; font-size: 36px; letter-spacing: 1px; }
  .front-wordmark .name-sub { display: block; font-size: 26px; letter-spacing: 1px; }

  .card-back {
    top: 632px;
    background: linear-gradient(110deg, var(--paper) 0%, var(--white) 50%, var(--paper-shade) 100%);
  }
  .back-wordmark {
    position: absolute;
    top: 50px;
    right: 52px;
    font-family: "Cinzel", Georgia, serif;
    font-weight: 600;
    color: var(--navy-ink);
    text-align: right;
    line-height: 1.05;
  }
  .back-wordmark .name-main { display: block; font-size: 51px; letter-spacing: 0.5px; }
  .back-wordmark .name-sub { display: block; font-size: 38px; letter-spacing: 0.5px; }

  .person {
    position: absolute;
    left: 53px;
    top: 220px;
  }
  .person-name { font-size: 28px; font-weight: 700; color: var(--navy-ink); }
  .person-title { font-size: 17px; color: var(--grey-text); margin-top: 4px; }

  .divider {
    position: absolute;
    left: 53px;
    right: 53px;
    top: 288px;
    height: 1.5px;
    background: var(--navy-ink);
  }
  .contact-list {
    position: absolute;
    left: 53px;
    top: 300px;
    list-style: none;
  }
  .contact-list li {
    display: flex;
    align-items: center;
    gap: 10px;
    height: 28px;
    font-size: 18px;
    color: var(--grey-text);
  }
  .contact-list svg { width: 16px; height: 16px; fill: var(--navy-ink); flex: none; }
  .address {
    position: absolute;
    right: 53px;
    top: 300px;
    font-style: normal;
    text-align: right;
    font-size: 18px;
    line-height: 28px;
    color: var(--grey-text);
  }
</style>
</head>
<body>
  <section class="card card-front">
    <div class="front-wordmark">
      <span class="name-main">BEACON HOSPITALITY</span>
      <span class="name-sub">REPS</span>
    </div>
  </section>

  <section class="card card-back">
    <div class="back-wordmark">
      <span class="name-main">BEACON HOSPITALITY</span>
      <span class="name-sub">REPS</span>
    </div>

    <div class="person">
      <p class="person-name">Daniel M. Ward</p>
      <p class="person-title">Co-Founder</p>
    </div>

    <div class="divider"></div>

    <ul class="contact-list">
      <li>
        <svg viewBox="0 0 16 16" aria-hidden="true"><path d="M3.2 1.5l2.3 2.6-1.2 1.6c.9 2 2.4 3.5 4.4 4.4l1.6-1.2 2.6 2.3-1.3 2.3C6.8 13.2 2.8 9.2 1 4.5z"/><path d="M9 1.5a5.5 5.5 0 0 1 5.5 5.5h-1.3A4.2 4.2 0 0 0 9 2.8zM9 4.2A2.8 2.8 0 0 1 11.8 7h-1.3A1.5 1.5 0 0 0 9 5.5z"/></svg>
        312-555-0147
      </li>
      <li>
        <svg viewBox="0 0 16 16" aria-hidden="true"><path d="M1 3.5h14v1L8 9 1 4.5z"/><path d="M1 6l7 4.4L15 6v6.5H1z"/></svg>
        info@beaconhospitalityreps.com
      </li>
      <li>
        <svg viewBox="0 0 16 16" aria-hidden="true"><circle cx="8" cy="8" r="7"/><path d="M1.5 8h13M8 1c-2.5 2.5-2.5 11.5 0 14M8 1c2.5 2.5 2.5 11.5 0 14M2.5 4.5h11M2.5 11.5h11" stroke="#fff" stroke-width="0.9" fill="none"/></svg>
        www.beaconhospitalityreps.com
      </li>
    </ul>

    <address class="address">
      240 West Lake Street,<br>
      Suite 1800<br>
      Chicago, IL 60601
    </address>
  </section>
</body>
</html>
```